Fitness Centre/Personal Trainer Business Card

We need a business card design for a company based in Singapore called 'Vigor Ledger'.

We are a team of Personal Trainers and we are planning to open our new training facility.

This design will also be printed/painted on the walls in our gym.

We are a new breed of personal trainers who take fitness seriously and holistically. We do not merely train our clients to be big and muscular.

We believe in wholeness. In our opinion, fitness should include: strength, speed, flexibility, mobility, stamina & agility. These are what we train for. Of course, nutrition/diet is key.

We use fitness tools such as kettlebells, QVL, Pylometric boxes, battling ropes, clubbells, medicine balls, bulgarian bags etc - functional and non-bulky tools.

I currently have a Facebook page 'Vigor Ledger SG' which shows a logo of a kettlebell. But my business focus has since changed.

Services provided:
- Kettlebell Sport Preparation
- Calisthenics Training
- Corrective Exercises
- Sports Strength & Conditioning
- 28 days Weight Loss Program
- Myofascial Rehab Therapy
- Sports/Thai Massage

Main colors for the design should be BLACK & YELLOW. We envision a design which is able to protray the holistic view we take on fitness. Also it should somewhat appeal to the ladies and not intimidate them.

Target Market(s)

People between 18-35 years old. Students and working class alike.

Industry/Entity Type

Training

Requirements
Must have
• Name: Marcus Obadiah Lim
Fitness Coach
Corrective Exercise Specialist
M: +65 9437 2065
E: marcus@sgvigorledger-example.com

Double-sided please.
Nice to have
• "What is your vigor ledger?"

```html
<!DOCTYPE html>
<html lang="en">
<head>
<meta charset="utf-8">
<title>Vigor Ledger – Business Cards</title>
<link rel="stylesheet" href="https://fonts.googleapis.com/css2?family=Open+Sans:wght@400;600;700&display=swap">
<style>
  :root {
    --yellow: #f5c400;
    --black: #050505;
    --grey: #5e5e5e;
    --white: #ffffff;
    --stage: #d9d6d0;
  }
  * { box-sizing: border-box; margin: 0; padding: 0; }
  html, body { width: 1200px; height: 722px; overflow: hidden; }
  body {
    background: var(--stage);
    font-family: "Open Sans", Arial, sans-serif;
    position: relative;
  }
  .card {
    position: absolute;
    width: 490px;
    height: 280px;
    border-radius: 14px;
    overflow: hidden;
    background: var(--black);
    color: var(--white);
  }
  .card--front { left: 92px; top: 64px; }
  .card--back-photo { left: 616px; top: 64px; }
  .card--back-grey { left: 92px; top: 378px; background: linear-gradient(160deg, #3c3c3c 0%, #262626 60%, #1c1c1c 100%); }
  .card--back-centred { left: 616px; top: 378px; }

  .wave { position: absolute; inset: 0; }

  .brand { position: absolute; text-align: center; }
  .brand__dot { display: block; margin: 0 auto; border-radius: 50%; background: var(--yellow); }
  .brand__name { display: block; font-weight: 700; color: var(--white); white-space: nowrap; }
  .brand__tagline { display: block; font-size: 11px; letter-spacing: 0.5px; color: var(--white); margin-top: 2px; white-space: nowrap; }

  .card--front .brand { left: 36px; top: 30px; width: 180px; }
  .card--front .brand__dot { width: 104px; height: 104px; }
  .card--front .brand__name { font-size: 25px; margin-top: 20px; }

  .photo-dumbbell {
    position: absolute; left: 296px; top: 24px; width: 100px; height: 52px; border-radius: 26px;
    background: radial-gradient(ellipse at 40% 35%, #f2f2f2 0%, #b9b9b9 45%, #5e5e5e 100%);
  }
  .person { position: absolute; left: 268px; top: 112px; white-space: nowrap; }
  .person__name { font-size: 17px; font-weight: 600; color: var(--yellow); letter-spacing: 0.2px; text-transform: uppercase; }
  .person__role { font-size: 12px; line-height: 17px; }
  .contact { position: absolute; left: 268px; top: 206px; list-style: none; font-size: 10.5px; line-height: 18px; }
  .contact li { display: flex; align-items: center; gap: 5px; white-space: nowrap; }
  .contact li:first-child { font-size: 14px; }
  .contact svg { width: 8px; height: 8px; fill: var(--yellow); flex: none; }

  .photo-weights {
    position: absolute; left: 30px; top: 120px; width: 310px; height: 150px;
    background: radial-gradient(ellipse at 45% 55%, #8a8a8a 0%, #3b3b3b 45%, #0a0a0a 80%);
  }
  .card--back-photo .brand { left: 88px; top: 14px; width: 90px; }
  .card--back-photo .brand__dot { width: 58px; height: 58px; }
  .card--back-photo .brand__name { font-size: 15px; margin-top: 8px; }

  .services-right { position: absolute; right: 15px; top: 36px; text-align: right; }
  .services__title { font-size: 17px; font-weight: 700; }
  .services-right ul { list-style: none; margin-top: 10px; }
  .services-right li { font-size: 14px; font-weight: 700; color: var(--yellow); line-height: 28px; }
  .services-right li::before, .services-list li::before, .services-grid span::before { content: "•"; margin-right: 3px; }

  .question { position: absolute; font-weight: 700; font-size: 15.5px; letter-spacing: 0.8px; text-transform: uppercase; white-space: nowrap; }
  .card--back-photo .question { left: 18px; top: 247px; }

  .card--back-grey .brand { left: 52px; top: 36px; width: 150px; }
  .card--back-grey .brand__dot { width: 104px; height: 104px; }
  .card--back-grey .brand__name { font-size: 23px; margin-top: 16px; }
  .card--back-grey .services__title { position: absolute; left: 252px; top: 24px; color: var(--yellow); }
  .services-list { position: absolute; left: 250px; top: 60px; list-style: none; }
  .services-list li { font-size: 14.5px; line-height: 24.7px; }
  .card--back-grey .question { left: 92px; top: 250px; color: var(--yellow); }

  .decor {
    position: absolute; left: 160px; top: 20px; width: 170px; height: 170px;
    border-radius: 50%; background: var(--yellow); opacity: 0.22;
  }
  .card--back-centred .services__title { position: absolute; left: 0; right: 0; top: 56px; text-align: center; font-size: 19px; }
  .services-grid {
    position: absolute; left: 0; right: 0; top: 104px; text-align: center; font-size: 17px; line-height: 31.5px;
  }
  .services-grid span { margin: 0 3px; }
  .card--back-centred .question { left: 0; right: 0; top: 248px; text-align: center; color: var(--yellow); }
</style>
</head>
<body>

<section class="card card--front">
  <svg class="wave" viewBox="0 0 490 280" preserveAspectRatio="none" aria-hidden="true">
    <path d="M0 168 C120 205 230 195 490 185 L490 280 L0 280 Z" fill="#5e5e5e"/>
    <path d="M0 162 C120 196 230 186 490 176 L490 185 C230 195 120 205 0 176 Z" fill="#f5c400"/>
  </svg>
  <div class="brand">
    <span class="brand__dot"></span>
    <span class="brand__name">Vigor Ledger</span>
    <span class="brand__tagline">Fitter Stronger Faster</span>
  </div>
  <div class="photo-dumbbell" role="img" aria-label="Photo of a chrome dumbbell"></div>
  <div class="person">
    <p class="person__name">Marcus Obadiah Lim</p>
    <p class="person__role">Fitness Coach<br>Corrective Exercise Specialist</p>
  </div>
  <ul class="contact">
    <li><svg viewBox="0 0 10 10"><rect x="2" y="0" width="6" height="10" rx="1.2"/></svg>+65 9437 2065</li>
    <li><svg viewBox="0 0 10 10"><rect x="0" y="2" width="10" height="7" rx="1"/></svg>marcus@sgvigorledger-example.com</li>
    <li><svg viewBox="0 0 10 10"><circle cx="5" cy="5" r="5"/></svg>www.sgvigorledger-example.com</li>
  </ul>
</section>

<section class="card card--back-photo">
  <div class="photo-weights" role="img" aria-label="Photo of hexagonal dumbbells on a dark floor"></div>
  <div class="brand">
    <span class="brand__dot"></span>
    <span class="brand__name">Vigor Ledger</span>
  </div>
  <div class="services-right">
    <p class="services__title">Services</p>
    <ul>
      <li>Sports Strength &amp; Conditioning</li>
      <li>Kettlebell Sport Preparation</li>
      <li>28 days Weight Loss Program</li>
      <li>Myofascial Rehab Therapy</li>
      <li>Calisthenics Training</li>
      <li>Corrective Exercises</li>
      <li>Sports/Thai Massage</li>
    </ul>
  </div>
  <p class="question">What is your vigor ledger ?</p>
</section>

<section class="card card--back-grey">
  <div class="brand">
    <span class="brand__dot"></span>
    <span class="brand__name">Vigor Ledger</span>
    <span class="brand__tagline">Fitter Stronger Faster</span>
  </div>
  <p class="services__title">Services</p>
  <ul class="services-list">
    <li>Sports Strength &amp; Conditioning</li>
    <li>Kettlebell Sport Preparation</li>
    <li>28 days Weight Loss Program</li>
    <li>Myofascial Rehab Therapy</li>
    <li>Calisthenics Training</li>
    <li>Corrective Exercises</li>
    <li>Sports/Thai Massage</li>
  </ul>
  <p class="question">What is your vigor ledger ?</p>
</section>

<section class="card card--back-centred">
  <div class="decor" aria-hidden="true"></div>
  <p class="services__title">Services</p>
  <div class="services-grid">
    <span>Sports Strength &amp; Conditioning</span> <span>Sports/Thai Massage</span><br>
    <span>Kettlebell Sport Preparation</span> <span>Corrective Exercises</span><br>
    <span>28 days Weight Loss Program</span> <span>Calisthenics Training</span><br>
    <span>Myofascial Rehab Therapy</span>
  </div>
  <p class="question">What is your vigor ledger ?</p>
</section>

</body>
</html>
```